Business Card Design

Business Card for professional consulting firm working with large financial institutions.

Target Market(s)

Executive buyers

Industry/Entity Type

Banking

Contact Information for Business Card

Mild creativity wanted. Not boring, but do elaborate artwork.

Font styles to use
Serif
Sans Serif

Colors

Designer to choose colors to be used in the design.

Requirements
Must have
• Standard business card features - company name, individual name, telephone, website, email, locations.
Nice to have
• Two colors
Should not have
• too many colors, fancy printing, cartoons.

```html
<!DOCTYPE html>
<html lang="en">
<head>
<meta charset="utf-8">
<title>Business Card – Halden Advisory</title>
<link href="https://fonts.googleapis.com/css2?family=Open+Sans:wght@400;600&display=swap" rel="stylesheet">
<style>
  :root {
    --backdrop: #2b2b2c;
    --card: #1e1f21;
    --text: #f2f2f2;
    --muted: #b9b9b9;
    --rule: #8a8a8a;
    --icon-fill: #c9c9c9;
    --pattern-a: #1e1f21;
    --pattern-b: #25262a;
  }
  * { margin: 0; padding: 0; box-sizing: border-box; }
  html, body { width: 1200px; height: 1108px; overflow: hidden; }
  body {
    background: var(--backdrop);
    font-family: "Open Sans", Arial, sans-serif;
    color: var(--text);
    position: relative;
  }
  .card {
    position: absolute;
    top: 214px;
    width: 400px;
    height: 680px;
    background: var(--card);
    border-radius: 22px;
    box-shadow: 0 18px 40px rgba(0,0,0,.45);
    overflow: hidden;
  }
  .card--front { left: 160px; }
  .card--back { left: 640px; }

  .front-brand {
    position: absolute;
    top: 138px; left: 0; right: 0;
    text-align: center;
    font-size: 24px;
    font-weight: 600;
    letter-spacing: 4px;
    text-transform: uppercase;
    color: var(--muted);
  }
  .holder {
    position: absolute;
    top: 300px; left: 0; right: 0;
    text-align: center;
  }
  .holder-name {
    font-size: 27px;
    font-weight: 600;
    letter-spacing: .5px;
    text-transform: uppercase;
  }
  .holder-title {
    font-size: 17px;
    color: var(--muted);
    margin-top: 2px;
  }
  .icon-rule {
    position: absolute;
    top: 382px; left: 70px; right: 70px;
    height: 26px;
  }
  .contact {
    position: absolute;
    top: 420px; left: 0; right: 0;
    text-align: center;
    font-size: 19px;
    line-height: 31px;
  }
  .divider {
    position: absolute;
    top: 530px; left: 90px; right: 90px;
    height: 1px;
    background: var(--rule);
  }
  .address {
    position: absolute;
    top: 548px; left: 0; right: 0;
    text-align: center;
    font-size: 19px;
    line-height: 29px;
  }

  .back-pattern {
    position: absolute;
    inset: 0;
    background: linear-gradient(175deg, var(--pattern-b) 0%, var(--pattern-a) 75%);
  }
  .back-brand {
    position: absolute;
    left: 0; right: 0; bottom: 110px;
    text-align: center;
    font-size: 30px;
    font-weight: 600;
    letter-spacing: 5px;
    text-transform: uppercase;
    color: var(--text);
  }
</style>
</head>
<body>
  <section class="card card--front">
    <div class="front-brand">Halden Advisory</div>

    <div class="holder">
      <div class="holder-name">Jonathan Smith</div>
      <div class="holder-title">Managing Director</div>
    </div>

    <svg class="icon-rule" viewBox="0 0 260 26" aria-hidden="true">
      <line x1="0" y1="13" x2="94" y2="13" stroke="#8a8a8a" stroke-width="1"/>
      <line x1="166" y1="13" x2="260" y2="13" stroke="#8a8a8a" stroke-width="1"/>
      <circle cx="106" cy="13" r="10" fill="#c9c9c9"/>
      <path d="M102 8 q1 -1 2 0 l1.5 2 q.5 1 -.5 1.5 q1 3 3.5 4.5 q.5 -1 1.5 -.5 l2 1.5 q1 1 0 2 q-2 2 -5 0 q-4 -3 -5.5 -7 q-1 -3 .5 -4z" fill="#1e1f21"/>
      <circle cx="130" cy="13" r="10" fill="#c9c9c9"/>
      <rect x="124" y="9" width="12" height="8" rx="1" fill="#1e1f21"/>
      <path d="M124.5 9.5 l5.5 4.5 l5.5 -4.5" stroke="#c9c9c9" stroke-width="1" fill="none"/>
      <circle cx="154" cy="13" r="10" fill="#c9c9c9"/>
      <path d="M154 20 q-5 -5 -5 -8.5 a5 5 0 0 1 10 0 q0 3.5 -5 8.5z" fill="#1e1f21"/>
      <circle cx="154" cy="11.5" r="1.8" fill="#c9c9c9"/>
    </svg>

    <div class="contact">
      <div class="contact-phone">444 555 6688</div>
      <div class="contact-email">info@youremail.com</div>
      <div class="contact-web">www.websitename.com</div>
    </div>

    <div class="divider"></div>

    <div class="address">
      <div>12345, Address Goes Here</div>
      <div>Country Name, 123456.</div>
    </div>
  </section>

  <section class="card card--back">
    <div class="back-pattern" role="img" aria-label="Faint tone-on-tone repeating pattern area"></div>
    <div class="back-brand">Halden Advisory</div>
  </section>
</body>
</html>
```